Tender / Request for Quotation response template

KELVARA42 is a small consulting company that works in management consulting with a particular emphasis on tourism, sport, major events and general commercial. our clients range from government , councils, private businesses and industry associations.

we are regularly asked to submit detailed quotes or tender responses and we use our own PowerPoint template to do so as we find it its generally easier to work with.

our website provides more detail : www.kelvara42.com.au the colour of the blue in logo is #000033

our submissions range from 30 pages to 100 pages depending on the size and scale of the project - so we need flexibility with the templates.

Our submissions generally include cover page and table of contents and then
1. Project overview
2. About KELVARA42
3. The project team including bios
4. Initial Insights
5. importance of sustainability
6. Project methodology - example being
6.1 situation analysis
- research
- consultation and engagement
- relevant audits
- relevant economic analysis including graphs
- gap analysis
- SWOT
6.2 Issues and opportunities
6.3 draft report
6.4 final report
7. Case studies and previous relevant work
8. Project timeline
9. Project budget
10. Insurance and referees

we use many graphs and tables from excel and images generally sourced from the web. we also use icons as appropriate so we need graph templates - column, bar / pie etc and table templates.

the feel is on the formal corporate side given the size and scale of projects and clients but with bright and clear graphics and photos.

i have attached 2 copies of confidential submissions that we have made in recent weeks. one long form and one short form to give you an idea of the flexibility we need in the submission process.

if we are happy with the proposed PowerPoint tender submission template we would then look to have a similar one created to use in the development of the actual reports themselves .

hopefully this provides enough information but if not please reach out for more information

our logo and general format are in the attached examples

Target Market(s)

government, council, corporates and private businesses

Industry/Entity Type

management consulting with emphasis on tourism sport major events nd general commerical

Other font styles liked:
• we usually use calbiri but open to other standard microsoft off the shelf fonts

Colors
0054AA
0677BA
7BADD7
CADEEF
E8F1F8
0094D4
00A9DD
6FCCEA
C7EBF8
E9F6FB

Requirements
Must have
• page for each of the sections detailed in the project brief. image placement - small and large, table and graph formats,

```html
<!DOCTYPE html>
<html lang="en">
<head>
<meta charset="utf-8">
<title>KELVARA42 Tender Response Template</title>
<link href="https://fonts.googleapis.com/css2?family=Arimo:wght@400;700&display=swap" rel="stylesheet">
<style>
:root{
  --canvas:#c3c3c3;
  --navy:#000033;
  --blue:#0072c4;
  --blue-deep:#0054aa;
  --blue-mid:#0677ba;
  --cyan:#0094d4;
  --pale:#cadeef;
  --row:#f3f3f3;
  --ink:#222;
  --white:#fff;
}
*{box-sizing:border-box;margin:0;padding:0}
html,body{width:1200px;height:1072px;overflow:hidden;background:var(--canvas);font-family:"Arimo",Arial,sans-serif;color:var(--ink)}
.board{position:relative;width:1200px;height:1072px}
.slide{position:absolute;width:545px;height:306px;background:var(--white);overflow:hidden}
.col-a{left:38px}.col-b{left:618px}
.row-1{top:45px}.row-2{top:380px}.row-3{top:721px}
.abs{position:absolute}

/* footer */
.footer{position:absolute;left:0;right:0;bottom:0;height:23px;background:linear-gradient(90deg,var(--cyan),var(--blue-mid) 60%,var(--blue-deep))}
.footer .copy{position:absolute;left:0;right:0;top:8px;text-align:center;font-size:4.6px;color:var(--white)}
.footer .page{position:absolute;right:17px;top:8px;font-size:4.6px;font-weight:700;color:var(--white)}
.brand-tab{position:absolute;left:0;bottom:0;width:32px;height:31px;background:var(--navy);display:flex;flex-direction:column;align-items:center;justify-content:center;gap:2px}
.brand-tab .dot{width:15px;height:15px;border:1.2px solid var(--white);border-radius:50%}
.brand-tab .name{font-size:5px;color:var(--white);letter-spacing:.2px}

.band{position:absolute;left:0;right:0;top:0;background:var(--blue)}
.band h2{color:var(--white);font-weight:700;font-size:22px;letter-spacing:.3px}

.photo{position:absolute}

/* cover */
.cover-photo{left:0;top:0;width:545px;height:306px;background:linear-gradient(135deg,#0b3f7c,#135fa6 55%,#0a4a8e)}
.cover-mark{left:0;right:0;top:10px;display:flex;flex-direction:column;align-items:center;gap:4px}
.cover-mark .ring{width:50px;height:50px;border:2px solid var(--white);border-radius:50%}
.cover-mark .name{font-size:16px;color:var(--white);letter-spacing:1px}
.cover-title{left:57px;top:112px;font-size:40px;font-weight:700;color:var(--white)}
.cover-sub{left:57px;top:168px;font-size:8.6px;font-weight:700;color:var(--white);line-height:14px}
.cover-frame{left:286px;top:170px;width:50px;height:49px;border-top:1.3px solid var(--white);border-left:1.3px solid var(--white)}
.cover-card{left:296px;top:180px;width:214px;height:79px;background:var(--white);padding:13px 12px;font-size:4.6px;font-weight:700;line-height:8.5px;text-align:justify;color:var(--ink)}
.cover-card p+p{margin-top:8px}

/* about */
.about-band{height:154px}
.about-side{position:absolute;right:0;top:0;width:31px;height:154px;background:var(--blue)}
.about-title{left:57px;top:40px;font-size:36px;font-weight:700;line-height:41px;color:var(--white)}
.about-photo{left:55px;top:133px;width:236px;height:127px;background:linear-gradient(120deg,#55657a,#b9b0a2 55%,#e4e1da)}
.about-card{left:291px;top:45px;width:223px;height:238px;background:var(--white);padding:15px 14px 0 13px}
.about-card h3{font-size:6.4px;font-weight:700;margin-bottom:14px}
.about-card ul{list-style:none}
.about-card li{position:relative;padding-left:11px;font-size:4.4px;line-height:7px;text-align:justify;color:#333;margin-bottom:7.3px}
.about-card li svg{position:absolute;left:0;top:1px;width:4.5px;height:4.5px}

/* toc */
.toc-band{height:53px;padding:15px 0 0 56px}
.toc{position:absolute;left:54px;top:70px;width:436px}
.toc-row{display:flex;height:18px;margin-bottom:1.8px;font-size:5.8px;font-weight:700;align-items:center}
.toc-row .num{width:22px;height:100%;background:var(--blue-mid);color:var(--white);display:flex;align-items:center;justify-content:center;font-weight:400}
.toc-row .label{flex:1;height:100%;background:var(--row);display:flex;align-items:center;padding-left:41px;margin-left:1px}
.toc-row .pg{width:28px;height:100%;background:var(--pale);display:flex;align-items:center;justify-content:center;margin-left:1px;font-weight:400}

/* team */
.team-band{height:49px;text-align:center;padding-top:11px}
.portrait{position:absolute;width:71px;height:73px;border:2px solid var(--navy);background:linear-gradient(160deg,#8a8fa6,#c9b8a8 60%,#5a6a80)}
.member{position:absolute;width:120px;text-align:center}
.member .name{font-size:8.4px;font-weight:700;color:var(--ink)}
.member .role{font-size:5.6px;color:var(--blue);margin-top:4px}

/* overview */
.overview-photo{left:0;top:0;width:545px;height:154px;background:linear-gradient(100deg,#0c2f58,#134d86 50%,#0e3d70)}
.overview-title{left:57px;top:38px;font-size:45px;font-weight:700;line-height:42px;color:var(--white)}
.overview-sub{left:57px;top:169px;font-size:13.6px;font-weight:700;line-height:17px;color:#2a2a2a}

/* insights */
.insight-band{height:49px;text-align:center;padding-top:11px}
.insight-photo{left:62px;top:72px;width:209px;height:183px;background:linear-gradient(135deg,#2c2c2c,#6b6660 50%,#c8c2b8)}
.insight-card{left:271px;top:72px;width:209px;height:183px;background:var(--blue);padding:50px 18px 0 18px;color:var(--white);font-size:4.4px;line-height:8.5px;text-align:justify}
.insight-card p+p{margin-top:8.5px}
</style>
</head>
<body>
<main class="board">

  <!-- Cover -->
  <section class="slide col-a row-1">
    <div class="photo abs cover-photo" role="img" aria-label="Team of consultants meeting around a table, blue tinted"></div>
    <div class="abs cover-mark"><span class="ring"></span><span class="name">KELVARA42</span></div>
    <h1 class="abs cover-title">KELVARA42</h1>
    <p class="abs cover-sub">YOUR COMPLETE CONSULTING AND BUSINESS<br>ADVISORY SOLUTION</p>
    <div class="abs cover-frame"></div>
    <div class="abs cover-card">
      <p>We are an innovative consulting and business advisory servicing both the public and private sector in Australia and New Zealand.</p>
      <p>Our clients include Government enterprises, councils, corporate groups, private equity, family businesses, industry associations, small businesses and not for profits.</p>
    </div>
  </section>

  <!-- About -->
  <section class="slide col-b row-1">
    <div class="band about-band"></div>
    <div class="about-side"></div>
    <h2 class="abs about-title">ABOUT<br>KELVARA42</h2>
    <div class="photo abs about-photo" role="img" aria-label="Two colleagues reviewing a tablet in an office"></div>
    <div class="abs about-card">
      <h3>We bring to this extremely important project:</h3>
      <ul>
        <li><svg viewBox="0 0 10 10"><circle cx="5" cy="5" r="5" fill="#0677ba"/><path d="M2.8 5.2l1.5 1.5 3-3.2" stroke="#fff" stroke-width="1.3" fill="none"/></svg>The most experienced project team in Australia in nature based tourism, events and the visitor economy. We understand the challenges and opportunities presented by utilising Crown land.</li>
        <li><svg viewBox="0 0 10 10"><circle cx="5" cy="5" r="5" fill="#0677ba"/><path d="M2.8 5.2l1.5 1.5 3-3.2" stroke="#fff" stroke-width="1.3" fill="none"/></svg>Each member of the project team and specialist team are experts in their field. They are not generalist consultants. All KELVARA42 project work will be undertaken by these experts and NOT delegated to an inexperienced junior consultant.</li>
        <li><svg viewBox="0 0 10 10"><circle cx="5" cy="5" r="5" fill="#0677ba"/><path d="M2.8 5.2l1.5 1.5 3-3.2" stroke="#fff" stroke-width="1.3" fill="none"/></svg>The project team are all industry leaders of high standing that will bring insights and outcomes based on over 100 years of collective experience.</li>
        <li><svg viewBox="0 0 10 10"><circle cx="5" cy="5" r="5" fill="#0677ba"/><path d="M2.8 5.2l1.5 1.5 3-3.2" stroke="#fff" stroke-width="1.3" fill="none"/></svg>Our team have all sat on both the client and consultant side. We know exactly what is required to deliver a successful outcome for the client. For that reason, we operate under a co-design model.</li>
        <li><svg viewBox="0 0 10 10"><circle cx="5" cy="5" r="5" fill="#0677ba"/><path d="M2.8 5.2l1.5 1.5 3-3.2" stroke="#fff" stroke-width="1.3" fill="none"/></svg>We bring extensive local knowledge of the Southern Cape Coast region, its visitor economy, its accommodation offerings and experience working with Aboriginal land custodians.</li>
        <li><svg viewBox="0 0 10 10"><circle cx="5" cy="5" r="5" fill="#0677ba"/><path d="M2.8 5.2l1.5 1.5 3-3.2" stroke="#fff" stroke-width="1.3" fill="none"/></svg>We have a laser like focus on stakeholder &amp; community participation both through direct engagement and by survey. We understand and have great respect of the need for Social Licence and Sustainability of outcomes.</li>
        <li><svg viewBox="0 0 10 10"><circle cx="5" cy="5" r="5" fill="#0677ba"/><path d="M2.8 5.2l1.5 1.5 3-3.2" stroke="#fff" stroke-width="1.3" fill="none"/></svg>We bring passion and energy to our projects. We love our industry and our jobs. We have fun ensuring the best outcomes for our clients.</li>
      </ul>
    </div>
    <footer class="footer"><span class="copy">© Copyrights Company name 2023. All rights reserved</span><span class="page">PAGE NO : 04</span></footer>
    <div class="brand-tab"><span class="dot"></span><span class="name">KELVARA42</span></div>
  </section>

  <!-- Table of contents -->
  <section class="slide col-a row-2">
    <div class="band toc-band"><h2>TABLE OF CONTENTS</h2></div>
    <div class="toc">
      <div class="toc-row"><span class="num">01</span><span class="label">PROJECT OVERVIEW</span><span class="pg">4</span></div>
      <div class="toc-row"><span class="num">02</span><span class="label">PROJECT TEAM</span><span class="pg">8</span></div>
      <div class="toc-row"><span class="num">03</span><span class="label">OUR PHILOSOPHY &amp; INITIAL ANALYSIS</span><span class="pg">21</span></div>
      <div class="toc-row"><span class="num">04</span><span class="label">OUR PROJECT METHODOLOGY</span><span class="pg">28</span></div>
      <div class="toc-row"><span class="num">05</span><span class="label">RELEVANT PROJECT EXPERIENCE</span><span class="pg">55</span></div>
      <div class="toc-row"><span class="num">06</span><span class="label">INDICATIVE PROJECT TIMELINE</span><span class="pg">67</span></div>
      <div class="toc-row"><span class="num">07</span><span class="label">PROJECT FEES</span><span class="pg">69</span></div>
      <div class="toc-row"><span class="num">08</span><span class="label">REFEREES AND INSURANCE</span><span class="pg">71</span></div>
      <div class="toc-row"><span class="num">09</span><span class="label">CONTACT DETAILS</span><span class="pg"></span></div>
    </div>
    <footer class="footer"><span class="copy">© Copyrights Company name 2023. All rights reserved</span><span class="page">PAGE NO : 02</span></footer>
    <div class="brand-tab"><span class="dot"></span><span class="name">KELVARA42</span></div>
  </section>

  <!-- Team -->
  <section class="slide col-b row-2">
    <div class="band team-band"><h2>THE PROJECT TEAM INCLUDES BIOS</h2></div>
    <div class="portrait" style="left:74px;top:71px" role="img" aria-label="Portrait of Martin Hale"></div>
    <div class="portrait" style="left:237px;top:71px" role="img" aria-label="Portrait of Dr Fiona Marsh"></div>
    <div class="portrait" style="left:401px;top:69px" role="img" aria-label="Portrait of Daniel Booth"></div>
    <div class="portrait" style="left:160px;top:166px" role="img" aria-label="Portrait of Graham Tully"></div>
    <div class="portrait" style="left:319px;top:167px" role="img" aria-label="Portrait of Helen Carver"></div>
    <div class="member" style="left:50px;top:152px"><div class="name">Martin Hale</div><div class="role">Project Manager</div></div>
    <div class="member" style="left:214px;top:152px"><div class="name">Dr Fiona Marsh</div><div class="role">Product Development</div></div>
    <div class="member" style="left:378px;top:152px"><div class="name">Daniel Booth</div><div class="role">Consumer Research</div></div>
    <div class="member" style="left:131px;top:248px"><div class="name">Graham Tully AM</div><div class="role">Event Strategy</div></div>
    <div class="member" style="left:295px;top:248px"><div class="name">Helen Carver</div><div class="role">Strategic Planning</div></div>
    <footer class="footer"><span class="copy">© Copyrights Company name 2023. All rights reserved</span><span class="page">PAGE NO : 05</span></footer>
    <div class="brand-tab"><span class="dot"></span><span class="name">KELVARA42</span></div>
  </section>

  <!-- Project overview -->
  <section class="slide col-a row-3">
    <div class="photo abs overview-photo" role="img" aria-label="Runners on a coastal road at dusk, blue tinted"></div>
    <h2 class="abs overview-title">PROJECT<br>OVERVIEW</h2>
    <p class="abs overview-sub">Development of Crown Land Utilisation Strategy<br>(to deliver SCCLA outcomes including local economic stimulation)</p>
    <footer class="footer"><span class="copy">© Copyrights Company name 2023. All rights reserved</span><span class="page">PAGE NO : 03</span></footer>
    <div class="brand-tab"><span class="dot"></span><span class="name">KELVARA42</span></div>
  </section>

  <!-- Initial insights -->
  <section class="slide col-b row-3">
    <div class="band insight-band"><h2>INITIAL INSIGHTS</h2></div>
    <div class="photo abs insight-photo" role="img" aria-label="Colleagues discussing around a laptop in a meeting room"></div>
    <div class="abs insight-card">
      <p>KELVARA42 has been very fortunate to be appointed by SCCLA to develop the new Caravan and Camping Plan Project (CCPP). This project is well advanced with the proposed Plan currently being written.</p>
      <p>There are a number of significant synergies across these projects which will enable a much deeper analysis for the Crown Lands Utilisation Strategy for the same budget, than if it was undertaken in isolation. As the timings of these projects will overlap, we believe it makes considerable sense to run them collectively to maximise the efficiencies and knowledge gained across and for both projects. These efficiencies are outlined below.</p>
    </div>
    <footer class="footer"><span class="copy">© Copyrights Company name 2023. All rights reserved</span><span class="page">PAGE NO : 06</span></footer>
    <div class="brand-tab"><span class="dot"></span><span class="name">KELVARA42</span></div>
  </section>

</main>
</body>
</html>
```